Website Development for vaultmerrow.com.au

Build a new Wordpress/Responsive website for vaultmerrow.com.au

Target Market(s)

Compliance Managers, Risk Managers, Information Security and Cyber Security Professionals, Chief Data/Digital Officers, Chief Operating/Financial Officers, Business Continuity Professionals, Disaster Recovery Planners, Small Business Owners, Local/Federal Government entities

Industry/Entity Type

Data Service

Coding

Coded - Design and coding required

Number of Pages Required

5+ page

Font styles to use
Sans Serif

Colors

Designer to choose colors to be used in the design.

Requirements
Must have
• 1. Site Structure: Home Page plus the following chapter-pages for a) Services b) About c) Resources d) Blog e) Contact Us
• 2. Prefer site to built on wordpress and we can purchase a theme if needed (we currently use Kelp9 for other sites)
• 3. Blog needs to be wordpress based
• 4. We will host the site ourselves on our own servers
• 5. Responsive Design
Nice to have
• 1. Livechat capability/interface
• 2. Capability for marketing automation integration (such as hubspot, marketo, infusionsoft etc)
• 3. Capability for CRM integration (Salesforce)

```html
<!DOCTYPE html>
<html lang="en">
<head>
<meta charset="utf-8">
<title>Vault Merrow — Protecting Your Data</title>
<link href="https://fonts.googleapis.com/css2?family=Montserrat:wght@600;700;800&family=Poppins:wght@300;400;500;600;700&display=swap" rel="stylesheet">
<style>
:root{
  --red:#e0001b;
  --red-deep:#b8000f;
  --red-dark:#8d0010;
  --ink:#111111;
  --night:#0b0b0d;
  --footer:#1b1b1d;
  --text:#555a60;
  --muted:#8a8f96;
  --white:#ffffff;
  --pale:#f3f5f9;
}
*{box-sizing:border-box;margin:0;padding:0}
html,body{width:1200px;height:4444px;overflow:hidden}
body{font-family:"Poppins",sans-serif;color:var(--ink);background:var(--white);position:relative}
.abs{position:absolute}
.center{left:0;width:1200px;text-align:center}

/* Hero */
.hero{top:0;left:0;width:1200px;height:631px;background:radial-gradient(circle at 62% 50%,#3a0308 0%,#170205 35%,var(--night) 70%);overflow:hidden}
.hero-art{left:560px;top:40px;width:560px;height:560px;border-radius:50%;background:radial-gradient(circle,rgba(224,0,27,.45) 0%,rgba(224,0,27,.12) 45%,transparent 70%)}
.brand{display:flex;align-items:center;gap:12px;font-family:"Poppins",sans-serif;font-weight:700;color:var(--red);letter-spacing:1px}
.brand-dot{width:30px;height:30px;border-radius:50%;background:var(--red)}
.hero .brand{left:100px;top:42px;font-size:32px}
.nav{right:108px;top:40px;display:flex;gap:36px;font-family:"Montserrat",sans-serif;font-weight:700;font-size:15px;color:var(--white);letter-spacing:.5px}
.hero-title{left:122px;top:225px;font-family:"Montserrat",sans-serif;font-weight:700;font-size:33px;line-height:60px;color:var(--white)}
.hero-title em{font-style:normal;color:var(--red)}
.btn{display:inline-block;border-radius:40px;font-family:"Montserrat",sans-serif;font-weight:700;font-size:14px;text-transform:uppercase;letter-spacing:.3px}
.hero .btn{left:132px;top:408px;width:334px;height:66px;line-height:66px;text-align:center;background:var(--white);color:var(--red);box-shadow:0 0 0 6px rgba(255,255,255,.18)}
.arrow{top:282px;width:30px;height:50px}

/* About */
.kicker{font-family:"Montserrat",sans-serif;font-weight:700;color:var(--red);font-size:17px;letter-spacing:1.5px}
.h2{font-family:"Montserrat",sans-serif;font-weight:800;color:var(--ink)}
.rule{width:46px;height:3px;background:var(--red);left:577px}
.about-bg{top:631px;left:0;width:1200px;height:1236px;background:linear-gradient(180deg,#fff 0%,#fff 30%,var(--pale) 100%)}
.about-text{left:310px;width:580px;top:815px;font-size:16px;line-height:30px;color:var(--text);text-align:center}
.device{left:415px;top:933px;width:430px;height:270px;border-radius:10px;background:linear-gradient(135deg,#2a2a30,#7a0010 55%,#e0001b);}
.about-btn{left:435px;top:1264px;width:330px;height:66px;line-height:66px;text-align:center;background:var(--red);color:var(--white);box-shadow:0 10px 24px rgba(224,0,27,.35)}
.quote-mark{left:222px;top:1390px;font-family:"Montserrat",sans-serif;font-weight:800;font-size:260px;line-height:1;color:#e9ebef}
.testimonial{left:326px;top:1490px;width:548px;height:243px;background:var(--white);box-shadow:0 14px 40px rgba(0,0,0,.12);border-bottom:4px solid var(--red);text-align:center}
.testimonial p{margin:62px 40px 0;font-size:15px;line-height:27px;color:var(--text)}
.testimonial .who{margin-top:16px;font-size:12px;font-weight:600;color:var(--ink)}
.testimonial .who b{color:var(--red);font-weight:600}
.avatar{left:557px;top:1446px;width:86px;height:86px;border-radius:50%;background:linear-gradient(#cfd3d8,#9aa0a6);border:5px solid var(--white);box-shadow:0 0 0 3px var(--red)}
.slider-dots{left:548px;top:1762px;display:flex;gap:8px;align-items:center;font-size:12px;color:var(--muted)}
.slider-dots i{width:6px;height:6px;border-radius:50%;background:#cfd3d8}
.slider-dots i.on{background:var(--ink)}
.chat-tab{left:1141px;top:936px;width:59px;height:205px;background:var(--red);border-radius:14px 0 0 14px}
.chat-tab span{position:absolute;left:14px;top:30px;writing-mode:vertical-rl;transform:rotate(180deg);color:var(--white);font-weight:700;font-size:15px;letter-spacing:2px}

/* Services */
.services{top:1867px;left:0;width:1200px;height:820px;background:linear-gradient(135deg,var(--red) 0%,var(--red-deep) 45%,#d10017 70%,var(--red-dark) 100%)}
.services .h2,.blog .h2{color:var(--white)}
.white-rule{width:46px;height:3px;background:var(--white);left:577px}
.sub-white{font-size:13px;line-height:22px;color:rgba(255,255,255,.92)}
.service-card{width:230px;height:208px;background:var(--white);box-shadow:0 12px 30px rgba(0,0,0,.22)}
.service-card .ico{position:absolute;left:26px;top:-26px;width:58px;height:58px;border-radius:50%;background:var(--ink);display:flex;align-items:center;justify-content:center}
.service-card h3{position:absolute;left:26px;top:50px;font-family:"Montserrat",sans-serif;font-weight:700;font-size:19px;line-height:22px;color:var(--ink)}
.service-card p{position:absolute;left:26px;right:24px;top:110px;font-size:11.5px;line-height:20px;color:var(--text)}
.service-card .go{position:absolute;right:20px;bottom:18px}

/* Resources */
.res-sub{left:460px;width:280px;top:2845px;font-size:16px;line-height:30px;color:var(--text);text-align:center}
.res-card{left:237px;top:2945px;width:726px;height:368px;background:var(--white);box-shadow:0 14px 40px rgba(0,0,0,.13)}
.res-photo{position:absolute;left:0;top:0;width:364px;height:368px;background:linear-gradient(135deg,#0e2a4a,#2f6c9c 55%,#8fc1e3)}
.res-ico{position:absolute;left:392px;top:42px;width:50px;height:50px;border-radius:50%;background:var(--red);display:flex;align-items:center;justify-content:center}
.res-card h3{position:absolute;left:392px;top:108px;font-family:"Montserrat",sans-serif;font-weight:700;font-size:17px}
.res-card p{position:absolute;left:392px;right:40px;top:140px;font-size:12.5px;line-height:21px;color:var(--text)}
.res-btn{position:absolute;left:392px;top:232px;width:196px;height:38px;line-height:34px;text-align:center;border:2px solid var(--red);color:var(--red);border-radius:30px;font-size:12px;letter-spacing:2px}
.pager{position:absolute;left:392px;top:305px;display:flex;gap:10px}
.pager span{width:22px;height:22px;border-radius:50%;border:1px solid #d5d8dc;font-size:11px;line-height:20px;text-align:center;color:var(--muted)}
.res-deco{left:930px;top:2780px;width:270px;height:560px;background:radial-gradient(circle at 70% 50%,rgba(224,0,27,.35),rgba(224,0,27,.08) 45%,transparent 70%)}

/* Blog */
.blog{top:3369px;left:0;width:1200px;height:720px;background:linear-gradient(135deg,var(--red-deep) 0%,var(--red) 40%,var(--red-dark) 100%)}
.blog-card{background:var(--white)}
.blog-card .img{position:absolute;background:linear-gradient(135deg,#0d1722,#274257 60%,#4d7a95)}
.blog-card h4{position:absolute;font-family:"Montserrat",sans-serif;font-weight:700;font-size:10.5px;color:var(--ink)}
.blog-card .date{position:absolute;font-size:9px;font-weight:600;color:var(--red)}
.blog-card p{position:absolute;font-size:9.5px;line-height:16px;color:var(--text)}
.share{position:absolute;display:flex;gap:6px}
.share i{width:18px;height:18px;border-radius:50%;border:1px solid #d5d8dc;display:block}
.share i.on{background:#1e88e5;border-color:#1e88e5}
.go-btn{left:570px;top:4026px;width:60px;height:42px;border:2px solid var(--white);color:var(--white);font-size:12px;font-weight:600;text-align:center;line-height:38px}

/* Footer */
.footer{top:4089px;left:0;width:1200px;height:355px;background:var(--footer)}
.footer .brand{left:0;width:1200px;justify-content:center;top:70px;font-size:54px}
.contact{top:4300px;display:flex;gap:14px}
.contact h5{font-size:11px;font-weight:700;color:var(--white);letter-spacing:.5px}
.contact div p{font-size:10px;line-height:15px;color:#bfc2c6}
.copyright{top:4404px;font-size:11px;color:#bfc2c6}
.chat-btn{left:30px;top:4385px;width:207px;height:59px;background:var(--red);border-radius:14px 14px 0 0;color:var(--white);font-weight:700;font-size:15px;letter-spacing:1px;display:flex;align-items:center;justify-content:center;gap:12px}
</style>
</head>
<body>

<!-- Hero -->
<section class="abs hero">
  <div class="abs hero-art" role="img" aria-label="Glowing red digital shield made of network points"></div>
  <div class="abs brand"><span class="brand-dot"></span>VAULT MERROW</div>
  <nav class="abs nav"><span>HOME</span><span>SERVICES</span><span>ABOUT</span><span>RESOURCES</span><span>BLOG</span><span>CONTACT</span></nav>
  <h1 class="abs hero-title">PROTECTING YOUR DATA<br><em>SECURITY</em> AND DATA <em>PRIVACY</em></h1>
  <a class="abs btn">Claim your free consultation</a>
  <svg class="abs arrow" style="left:38px" viewBox="0 0 30 50"><path d="M24 4 6 25l18 21" fill="none" stroke="#fff" stroke-width="3"/></svg>
  <svg class="abs arrow" style="left:1132px" viewBox="0 0 30 50"><path d="M6 4l18 21L6 46" fill="none" stroke="#fff" stroke-width="3"/></svg>
</section>

<!-- About -->
<section class="abs about-bg"></section>
<div class="abs center kicker" style="top:678px">WHO WE ARE</div>
<h2 class="abs center h2" style="top:708px;font-size:46px">ABOUT US</h2>
<div class="abs rule" style="top:776px"></div>
<p class="abs about-text">Maybe you've hired someone in the past to create your website, only to find out they know everything about pretty fonts and nothing about designs that convert. Perhaps you've worked with a content creator who writes</p>
<div class="abs device" role="img" aria-label="Laptop and phone showing the website with a video play button"></div>
<svg class="abs" style="left:556px;top:1020px" width="70" height="70" viewBox="0 0 70 70"><circle cx="35" cy="35" r="30" fill="none" stroke="#fff" stroke-width="3"/><path d="M28 22l20 13-20 13z" fill="#fff"/></svg>
<a class="abs btn about-btn">Claim your free consultation</a>

<div class="abs quote-mark">&ldquo;</div>
<div class="abs testimonial">
  <p>Lorem Ipsum is simply dummy text of the printing and typesetting industry. Lorem Ipsum has been the industry's standard dummy text ever since the 1500s. Sed ut perspiciatis unde omnis iste natus erro</p>
  <div class="who"><b>John Doe</b> – CEO at ABC Software</div>
</div>
<div class="abs avatar" role="img" aria-label="Portrait of the client giving the testimonial"></div>
<div class="abs slider-dots"><span>&lsaquo;</span><i class="on"></i><i></i><i></i><i></i><i></i><span>&rsaquo;</span></div>
<div class="abs chat-tab"><span>LIVE CHAT</span>
  <svg style="position:absolute;left:12px;top:160px" width="34" height="30" viewBox="0 0 34 30"><path d="M4 4h26v16H14l-7 6v-6H4z" fill="#fff"/></svg>
</div>

<!-- Services -->
<section class="abs services" role="img" aria-label="Red faceted low-poly background"></section>
<h2 class="abs center h2" style="top:1944px;font-size:30px">Our Services</h2>
<div class="abs white-rule" style="top:1996px"></div>
<p class="abs center sub-white" style="top:2026px">We'll do everything we can to grow your revenue. Our motivation<br>is to drive your business further that you can imagine.</p>

<div class="abs service-card" style="left:237px;top:2124px">
  <div class="ico"><svg width="26" height="26" viewBox="0 0 26 26"><rect x="5" y="11" width="16" height="12" rx="2" fill="#fff"/><path d="M8 11V8a5 5 0 0110 0v3" fill="none" stroke="#fff" stroke-width="2.4"/></svg></div>
  <h3>Cyber<br>Security</h3>
  <p>Lorem Ipsum is simply dummy text of the printing and typesetting industry.</p>
  <svg class="go" width="26" height="26" viewBox="0 0 26 26"><circle cx="13" cy="13" r="11" fill="none" stroke="#e0001b" stroke-width="1.6"/><path d="M7 13h11m-4-4l4 4-4 4" fill="none" stroke="#e0001b" stroke-width="1.6"/></svg>
</div>
<div class="abs service-card" style="left:486px;top:2124px">
  <div class="ico"><svg width="26" height="26" viewBox="0 0 26 26"><rect x="4" y="4" width="18" height="13" rx="1.5" fill="none" stroke="#fff" stroke-width="2"/><path d="M9 22h8M13 17v5" stroke="#fff" stroke-width="2"/></svg></div>
  <h3>Information<br>Security</h3>
  <p>Lorem Ipsum is simply dummy text of the printing and typesetting industry.</p>
  <svg class="go" width="26" height="26" viewBox="0 0 26 26"><circle cx="13" cy="13" r="11" fill="none" stroke="#e0001b" stroke-width="1.6"/><path d="M7 13h11m-4-4l4 4-4 4" fill="none" stroke="#e0001b" stroke-width="1.6"/></svg>
</div>
<div class="abs service-card" style="left:735px;top:2124px">
  <div class="ico"><svg width="26" height="26" viewBox="0 0 26 26"><path d="M6 3h10l5 5v15H6z" fill="none" stroke="#fff" stroke-width="2"/><path d="M10 14h7M10 18h7" stroke="#fff" stroke-width="2"/></svg></div>
  <h3>Disaster<br>Recovery</h3>
  <p>Lorem Ipsum is simply dummy text of the printing and typesetting industry.</p>
  <svg class="go" width="26" height="26" viewBox="0 0 26 26"><circle cx="13" cy="13" r="11" fill="none" stroke="#e0001b" stroke-width="1.6"/><path d="M7 13h11m-4-4l4 4-4 4" fill="none" stroke="#e0001b" stroke-width="1.6"/></svg>
</div>
<div class="abs service-card" style="left:358px;top:2394px">
  <div class="ico"><svg width="26" height="26" viewBox="0 0 26 26"><rect x="4" y="5" width="18" height="16" rx="1.5" fill="none" stroke="#fff" stroke-width="2"/><path d="M4 10h18" stroke="#fff" stroke-width="2"/></svg></div>
  <h3>Compliance<br>Management</h3>
  <p>Lorem Ipsum is simply dummy text of the printing and typesetting industry.</p>
  <svg class="go" width="26" height="26" viewBox="0 0 26 26"><circle cx="13" cy="13" r="11" fill="none" stroke="#e0001b" stroke-width="1.6"/><path d="M7 13h11m-4-4l4 4-4 4" fill="none" stroke="#e0001b" stroke-width="1.6"/></svg>
</div>
<div class="abs service-card" style="left:610px;top:2394px">
  <div class="ico"><svg width="26" height="26" viewBox="0 0 26 26"><rect x="4" y="7" width="18" height="14" rx="1.5" fill="none" stroke="#fff" stroke-width="2"/><circle cx="13" cy="14" r="3" fill="#fff"/></svg></div>
  <h3>Data<br>Security</h3>
  <p>Lorem Ipsum is simply dummy text of the printing and typesetting industry.</p>
  <svg class="go" width="26" height="26" viewBox="0 0 26 26"><circle cx="13" cy="13" r="11" fill="none" stroke="#e0001b" stroke-width="1.6"/><path d="M7 13h11m-4-4l4 4-4 4" fill="none" stroke="#e0001b" stroke-width="1.6"/></svg>
</div>

<!-- Resources -->
<div class="abs res-deco" role="img" aria-label="Soft red circuit decoration"></div>
<h2 class="abs center h2" style="top:2766px;font-size:30px">Our Resources</h2>
<div class="abs rule" style="top:2818px"></div>
<p class="abs res-sub">Lorem Ipsum is simply dummy text the printing and typesetting industry.</p>
<div class="abs res-card">
  <div class="res-photo" role="img" aria-label="Professional in a suit working on a laptop with digital padlock graphics"></div>
  <div class="res-ico"><svg width="22" height="22" viewBox="0 0 22 22"><path d="M13 1 4 13h6l-2 8 10-12h-6z" fill="#fff"/></svg></div>
  <h3>Cyber Security Professionals</h3>
  <p>Lorem Ipsum is simply dummy text of the printing and typesetting industry. Lorem Ipsum has been the industry's standard dummy text ever since the 1500s, when an unknown printer.</p>
  <div class="res-btn">DOWNLOAD NOW</div>
  <div class="pager"><span>&lsaquo;</span><span>&rsaquo;</span></div>
</div>

<!-- Blog -->
<section class="abs blog" role="img" aria-label="Red faceted low-poly background"></section>
<h2 class="abs center h2" style="top:3420px;font-size:30px;color:#fff">Our Blog</h2>
<div class="abs white-rule" style="top:3472px"></div>

<div class="abs blog-card" style="left:237px;top:3564px;width:356px;height:187px">
  <div class="img" style="left:0;top:0;width:124px;height:187px" role="img" aria-label="Person typing code on a laptop"></div>
  <h4 style="left:140px;top:14px">LOREM IPSUM IS SIMPLY DUMMY TEXT</h4>
  <div class="date" style="left:140px;top:34px">12 APR, 2019</div>
  <p style="left:140px;right:14px;top:58px">Lorem Ipsum is simply dummy text of the printing and typesetting industry. Lorem Ipsum has been the industry's standard dummy text ever since the 1500s.</p>
  <div class="share" style="left:140px;top:152px"><i></i><i class="on"></i><i></i><i></i></div>
</div>
<div class="abs blog-card" style="left:237px;top:3769px;width:356px;height:189px">
  <div class="img" style="left:0;top:0;width:124px;height:189px;background:linear-gradient(135deg,#0a1a33,#1f4f8f 60%,#7ab6f0)" role="img" aria-label="Hand touching a glowing digital padlock"></div>
  <h4 style="left:140px;top:14px">LOREM IPSUM IS SIMPLY DUMMY TEXT</h4>
  <div class="date" style="left:140px;top:34px">12 APR, 2019</div>
  <p style="left:140px;right:14px;top:58px">Lorem Ipsum is simply dummy text of the printing and typesetting industry. Lorem Ipsum has been the industry's standard dummy text ever since the 1500s.</p>
  <div class="share" style="left:140px;top:156px"><i></i></div>
</div>
<div class="abs blog-card" style="left:610px;top:3564px;width:353px;height:394px">
  <div class="img" style="left:0;top:0;width:353px;height:200px;background:linear-gradient(135deg,#05121c,#17394d 55%,#3f7590)" role="img" aria-label="Hooded figure at a desk of monitors in a dark room"></div>
  <h4 style="left:16px;top:220px">LOREM IPSUM IS SIMPLY DUMMY TEXT</h4>
  <div class="date" style="left:16px;top:240px">12 APR, 2019</div>
  <p style="left:16px;right:18px;top:264px">Lorem Ipsum is simply dummy text of the printing and typesetting industry. Lorem Ipsum has been the industry's standard dummy text ever since the 1500s, when an unknown.</p>
  <div class="share" style="left:16px;top:356px"><i></i></div>
</div>
<div class="abs go-btn">GO &rsaquo;</div>

<!-- Footer -->
<footer class="abs footer">
  <div class="abs brand"><span class="brand-dot" style="width:48px;height:48px"></span>VAULT MERROW</div>
</footer>
<div class="abs contact" style="left:272px">
  <svg width="32" height="24" viewBox="0 0 32 24"><rect x="1" y="1" width="30" height="22" fill="none" stroke="#e0001b" stroke-width="2"/><path d="M1 1l15 12L31 1" fill="none" stroke="#e0001b" stroke-width="2"/></svg>
  <div><h5>EMAIL</h5><p>info@vaultmerrow.com.au</p></div>
</div>
<div class="abs contact" style="left:522px">
  <svg width="24" height="32" viewBox="0 0 24 32"><rect x="2" y="1" width="20" height="30" rx="3" fill="none" stroke="#e0001b" stroke-width="2"/><path d="M9 26h6" stroke="#e0001b" stroke-width="2"/></svg>
  <div><h5>CALL US :</h5><p>+123 456 7890<br>+123 456 7890</p></div>
</div>
<div class="abs contact" style="left:738px">
  <svg width="26" height="32" viewBox="0 0 26 32"><path d="M13 30S3 18 3 11a10 10 0 0120 0c0 7-10 19-10 19z" fill="none" stroke="#e0001b" stroke-width="2"/><circle cx="13" cy="11" r="4" fill="none" stroke="#e0001b" stroke-width="2"/></svg>
  <div><h5>ADDRESS</h5><p>123, Main Road, New City,<br>My Country 123456</p></div>
</div>
<div class="abs center copyright">Copyright 2019. All rights reserved</div>
<div class="abs chat-btn">
  <svg width="34" height="28" viewBox="0 0 34 28"><path d="M3 3h28v16H14l-7 6v-6H3z" fill="#fff"/></svg>LIVE CHAT
</div>

</body>
</html>
```